VENTURE CAPITAL GROUP BUSINESS CARD DESIGN

Venture Capital Group based in SF looking for a bold business card design. No trendy colour explosion, 3D effects etc. Just "simple" optical effects. Works on your brain, keeps your eye focused and sticks to your mind.
Target Market(s)
Technology startups
Industry/Entity Type
Venture Capital
Contact Information for Business Card
DESMOND WHITLAKE
MANAGING PARTNER
187 FENWORTH ST SAN FRANCISCO, CA 94187
415.555.0142 O
415.555.0147 F
415.555.0193 C
desmond@veldtmoorcapital.ventures

```html
<!DOCTYPE html>
<html lang="en">
<head>
<meta charset="utf-8">
<title>Veldtmoor Capital Group – Business Card</title>
<link rel="stylesheet" href="https://fonts.googleapis.com/css2?family=Open+Sans:wght@400;600;700&display=swap">
<style>
  :root {
    --page-bg: #2b2b2b;
    --card-black: #050505;
    --brand-green: #3dbb3d;
    --logo-green: #2f9a3a;
    --band-gray: #b9babc;
    --disc-gray: #e6e6e6;
    --text-white: #ffffff;
  }
  * { margin: 0; padding: 0; box-sizing: border-box; }
  html, body {
    width: 1200px;
    height: 900px;
    overflow: hidden;
    background: var(--page-bg);
    font-family: "Open Sans", Arial, sans-serif;
  }
  .sheet {
    width: 1200px;
    height: 900px;
    display: flex;
    flex-direction: column;
    align-items: center;
    justify-content: center;
    gap: 40px;
  }
  .card {
    position: relative;
    width: 680px;
    height: 390px;
    background: var(--card-black);
    border-radius: 22px;
    overflow: hidden;
  }
  .card-bands {
    position: absolute;
    inset: 0;
    width: 100%;
    height: 100%;
  }
  .band-gray { fill: var(--band-gray); }
  .band-green { fill: var(--brand-green); }

  /* Brand name lockup */
  .brand {
    position: absolute;
    color: var(--logo-green);
    font-weight: 600;
    text-align: center;
    line-height: 1;
  }
  .brand-disc {
    border-radius: 50%;
    background: var(--disc-gray);
    margin: 0 auto;
  }
  .brand-name { display: block; letter-spacing: 0.04em; }
  .brand-sub { display: block; letter-spacing: 0.35em; }

  .card-front .brand { left: 0; right: 0; top: 40px; }
  .card-front .brand-disc { width: 120px; height: 120px; margin-bottom: 22px; }
  .card-front .brand-name { font-size: 40px; }
  .card-front .brand-sub { font-size: 11px; margin-top: 6px; }

  .card-back .brand { left: 60px; top: 36px; width: 210px; }
  .card-back .brand-disc { width: 96px; height: 96px; margin-bottom: 14px; }
  .card-back .brand-name { font-size: 27px; }
  .card-back .brand-sub { font-size: 8px; margin-top: 4px; }

  /* Person */
  .person {
    position: absolute;
    right: 40px;
    top: 112px;
    text-align: right;
  }
  .person-name {
    color: var(--text-white);
    font-weight: 700;
    font-size: 25px;
    letter-spacing: 0.04em;
    padding-bottom: 4px;
    border-bottom: 1.5px solid var(--text-white);
  }
  .person-title {
    color: var(--brand-green);
    font-weight: 600;
    font-size: 13px;
    letter-spacing: 0.06em;
    margin-top: 3px;
  }

  /* Contact */
  .contact {
    position: absolute;
    left: 60px;
    top: 196px;
    color: var(--text-white);
    font-size: 15px;
    line-height: 1.3;
  }
  .address {
    font-style: normal;
    margin-bottom: 6px;
  }
  .contact-list { list-style: none; }
  .contact-item {
    display: flex;
    align-items: center;
    gap: 10px;
  }
  .contact-icon {
    width: 12px;
    height: 12px;
    fill: var(--brand-green);
    flex: none;
  }
</style>
</head>
<body>
<main class="sheet">

  <!-- Front -->
  <section class="card card-front">
    <svg class="card-bands" viewBox="0 0 680 390" aria-hidden="true">
      <polygon class="band-gray" points="0,318 232,318 262,345 262,390 0,390"/>
      <polygon class="band-green" points="246,330 680,330 680,344 262,344"/>
    </svg>
    <div class="brand">
      <div class="brand-disc"></div>
      <span class="brand-name">VELDTMOOR</span>
      <span class="brand-sub">CAPITAL GROUP</span>
    </div>
  </section>

  <!-- Back -->
  <section class="card card-back">
    <svg class="card-bands" viewBox="0 0 680 390" aria-hidden="true">
      <polygon class="band-gray" points="680,318 448,318 418,345 418,390 680,390"/>
      <polygon class="band-green" points="0,330 434,330 418,344 0,344"/>
    </svg>

    <div class="brand">
      <div class="brand-disc"></div>
      <span class="brand-name">VELDTMOOR</span>
      <span class="brand-sub">CAPITAL GROUP</span>
    </div>

    <div class="person">
      <div class="person-name">DESMOND WHITLAKE</div>
      <div class="person-title">MANAGING PARTNER</div>
    </div>

    <div class="contact">
      <address class="address">187 FENWORTH ST SAN<br>FRANCISCO, CA 94187</address>
      <ul class="contact-list">
        <li class="contact-item">
          <svg class="contact-icon" viewBox="0 0 12 12"><path d="M2.5 0.5 L4.5 0.5 L5.2 3.2 L3.9 4.3 C4.6 5.8 6.2 7.4 7.7 8.1 L8.8 6.8 L11.5 7.5 L11.5 9.5 C11.5 10.6 10.6 11.5 9.5 11.5 C4.5 11.2 0.8 7.5 0.5 2.5 C0.5 1.4 1.4 0.5 2.5 0.5 Z"/></svg>
          <span>415.555.0142</span>
        </li>
        <li class="contact-item">
          <svg class="contact-icon" viewBox="0 0 12 12"><rect x="3" y="0.5" width="6" height="3"/><rect x="0.5" y="4" width="11" height="5" rx="1"/><rect x="3" y="8" width="6" height="3.5"/></svg>
          <span>415.555.0147</span>
        </li>
        <li class="contact-item">
          <svg class="contact-icon" viewBox="0 0 12 12"><path d="M3 0.5 H9 V11.5 H3 Z M4 1.8 V9 H8 V1.8 Z"/><circle cx="6" cy="10.2" r="0.6"/></svg>
          <span>415.555.0193</span>
        </li>
        <li class="contact-item">
          <svg class="contact-icon" viewBox="0 0 12 12"><path d="M0.5 2 H11.5 V10 H0.5 Z M1.5 3 V9 H10.5 V3 L6 6.5 Z"/></svg>
          <span>desmond@veldtmoorcapital.ventures</span>
        </li>
      </ul>
    </div>
  </section>

</main>
</body>
</html>
```